Request for Business Card Design

Hi. My name is Marlene, I am looking for a new business card design for my company, Quarrow Signal Instruments, LLC. I really like the design you did for Tarsel Venture and was hoping you could do something similar using our full logo and our mark. I am also open to any raised texture design using our mark. I have attached our full logo, which would need to be somewhere on the card, as well as the mark in both outline and full form, as well as our brand colors / guide. The card does not have to be white, as long as our logo and mark appear. I actually like darker colored business cards more, but am open to all options. If you are interested in working with me, please let me know. We would also take the business card design into letterhead design if you can do that.

```html
<!DOCTYPE html>
<html lang="en">
<head>
<meta charset="utf-8">
<title>Quarrow Signal Instruments — Business Card</title>
<link rel="stylesheet" href="https://fonts.googleapis.com/css2?family=Saira:wght@700&family=Arimo:wght@400&display=swap">
<style>
  :root {
    --backdrop: #141414;
    --card: #242424;
    --card-edge: #0094bd;
    --accent: #0096bf;
    --ink: #ffffff;
    --ink-soft: #e8e8e8;
  }
  * { margin: 0; padding: 0; box-sizing: border-box; }
  html, body {
    width: 1200px; height: 963px; overflow: hidden;
    background: var(--backdrop);
  }
  .stage {
    position: relative; width: 1200px; height: 963px;
    display: flex; align-items: center; justify-content: center;
  }
  .card {
    position: relative; width: 1000px; height: 572px;
    background: var(--card);
    border-radius: 34px;
    border-bottom: 4px solid var(--card-edge);
    overflow: hidden;
  }
  .brand {
    position: absolute; left: 120px; top: 70px;
    font-family: "Saira", sans-serif; font-weight: 700;
    color: var(--ink); line-height: 1;
  }
  .brand-name { font-size: 84px; letter-spacing: 10px; }
  .brand-tag { font-size: 21px; letter-spacing: 1.5px; margin-top: 6px; margin-left: -30px; }
  .rule {
    position: absolute; left: 60px; top: 300px; z-index: 1;
    width: 880px; height: 2px; background: var(--accent);
  }
  .brand-dot {
    position: absolute; left: 670px; top: 200px; z-index: 2;
    width: 240px; height: 240px; border-radius: 50%;
    background: var(--accent);
  }
  .person {
    position: absolute; left: 80px; top: 232px;
  }
  .person-name {
    font-family: "Saira", sans-serif; font-weight: 700;
    font-size: 34px; letter-spacing: 1px; color: var(--accent);
    text-transform: uppercase; line-height: 1; margin-left: 20px;
  }
  .person-role {
    font-family: "Arimo", sans-serif; font-size: 24px;
    color: var(--ink-soft); margin-top: 2px;
  }
  .contact {
    position: absolute; left: 60px; top: 322px;
    list-style: none;
    font-family: "Arimo", sans-serif; font-size: 25px; color: var(--ink);
  }
  .contact li { display: flex; align-items: center; gap: 14px; height: 42px; }
  .contact svg { width: 22px; height: 22px; flex: none; }
  .address {
    position: absolute; right: 80px; bottom: 34px;
    font-family: "Arimo", sans-serif; font-style: normal;
    font-size: 26px; color: var(--ink); line-height: 1.25;
  }
  .address span { display: block; }
  .address .line-two { margin-left: 6px; }
</style>
</head>
<body>
<main class="stage">
  <article class="card">
    <header class="brand">
      <div class="brand-name">QUARROW</div>
      <div class="brand-tag">SIGNAL INSTRUMENTS</div>
    </header>

    <section class="person">
      <h1 class="person-name">Elias Marwood</h1>
      <p class="person-role">Manager</p>
    </section>

    <div class="rule" aria-hidden="true"></div>
    <div class="brand-dot" aria-hidden="true"></div>

    <ul class="contact">
      <li>
        <svg viewBox="0 0 24 24" fill="none" stroke="#0096bf" stroke-width="2" stroke-linecap="round" stroke-linejoin="round" aria-hidden="true">
          <path d="M5 3h4l2 5-2.5 1.5a11 11 0 0 0 6 6L16 13l5 2v4a2 2 0 0 1-2 2A16 16 0 0 1 3 5a2 2 0 0 1 2-2z"/>
        </svg>
        <span>555-204-7139</span>
      </li>
      <li>
        <svg viewBox="0 0 24 24" fill="none" stroke="#0096bf" stroke-width="2" stroke-linejoin="round" aria-hidden="true">
          <rect x="2" y="5" width="20" height="14" rx="1"/>
          <path d="M2 6l10 7 10-7"/>
        </svg>
        <span>hello@quarrowsignal.com</span>
      </li>
      <li>
        <svg viewBox="0 0 24 24" fill="none" stroke="#0096bf" stroke-width="2" aria-hidden="true">
          <circle cx="12" cy="12" r="10"/>
          <path d="M2 12h20M12 2c3 3 3 17 0 20M12 2c-3 3-3 17 0 20"/>
        </svg>
        <span>www.quarrowsignal.com</span>
      </li>
    </ul>

    <address class="address">
      <span>Your Address, City</span>
      <span class="line-two">State, Zip 0000</span>
    </address>
  </article>
</main>
</body>
</html>
```